Two Versions of a Business Card for a Lawyer

Summary: I need a logo and a business card. The business card is two-sided and comes in two versions. One version is conservative, the other is slightly different with one or more pink embellishments in the logo or somewhere else in the business card.
I'm about to start off as a sole practitioner in criminal and immigration law. I'll largely be working with marginalised communities and in areas of social justice. One of my main focuses will be gendered violence, I'm hoping to specialise my practice towards representing victims of domestic and sexual violence and sex workers. I want a business card which would attract this clientele and make them feel safe to speak with me. I'd also like it to communicate a sense of hope.
However, the business card still has to be very conservative as the legal profession is very stuffy. So I was thinking of having two versions of the same card, one would be very straight forward while the other would have a **pink embellishment** or perhaps several. For example, if the scales of justice were used in the design, maybe the second version would have a pink flower about to bloom on the scale somewhere. Or maybe it's my logo that is different and pink.
While both designs have to be pretty conservative, I still want it to give off a sense that I'm alternative and think outside the box. With lawyers, I think a little bit of deviation goes a long way (less is more).
As far as colour goes (other than the pink embellishment), I was thinking something monochromatic, probably black and white but I am open to considering more colours. I personally love colour, and would love to use more colour, but am hesitant because of the nature of the profession. If you can find a way to use more colour while keeping it conservative and letting the pink pop, I'd be pretty pleased.
In general, I would prefer a clean simplistic design and logo. It should be immediately obvious that I'm a lawyer just by glancing at the card. I'm open to symbols of law, like the scales of justice or lady justice or something else. However, I don't want it to be the same as everyone else's.
Eventually, the design/style should be easy to recreate in the form of a website.
As far as the logo goes, it would probably use a circle as my last name starts with the letter "O". It can be very simple, with just my name and "Barrister & Solicitor". I don't currently have a logo, but the winning designer will be invited to provide a separate file for just the logo for an additional fee (I think it was CA$99). (Please ignore the uploaded logo file, it just wouldn't let me continue without uploading something).
As for the information that should go into the card, I'm still finalizing my address and phone number. So please use a placeholder for now.
Target Market(s)
Women, victims of sexual or domestic violence, refugees, people in need of legal services
Industry/Entity Type
Lawyer
Contact Information for Business Card
Marla Vent
Barrister & Solicitor
LL.B., B.C.L., B.F.A.
Criminal & Immigration Law
Street address
Toronto, ON
Postal Code
Phone number
Fax number
Email
Logo Text
Marla Vent, Barrister & Solicitor
Requirements
Must have
- Two versions
- One with pink
- Simplistic
Nice to have
- Maybe more colour
Should not have
- Not too conservative
- Not too predictable

```html
<!DOCTYPE html>
<html lang="en">
<head>
<meta charset="utf-8">
<title>Marla Vent – Business Cards</title>
<link rel="stylesheet" href="https://fonts.googleapis.com/css2?family=Didact+Gothic&display=swap">
<style>
  :root {
    --stage: #3f4b50;
    --card: #ffffff;
    --pink: #ee2ef0;
    --plum: #3d0a3d;
    --ink: #111111;
    --slate: #4d5a5e;
    --slate-band: #6b7b7a;
    --rule: #5f6b6c;
  }
  html, body {
    margin: 0;
    width: 832px;
    height: 1200px;
    overflow: hidden;
    background: var(--stage);
    font-family: "Didact Gothic", "Century Gothic", sans-serif;
  }
  .card {
    position: absolute;
    width: 359px;
    height: 538px;
    background: var(--card);
    overflow: hidden;
  }
  .card--front-pink { left: 33px; top: 38px; }
  .card--back-pink { left: 438px; top: 38px; }
  .card--front-mono { left: 33px; top: 634px; }
  .card--back-mono { left: 436px; top: 634px; }

  .card__band {
    position: absolute;
    left: 0; right: 0; bottom: 0;
    height: 39px;
    background: var(--pink);
  }
  .theme-mono .card__band { background: var(--slate-band); }

  /* Front */
  .logo-art {
    position: absolute;
    left: 215px; top: 94px;
    width: 88px; height: 200px;
    border-radius: 60% 40% 10% 50%;
    background: linear-gradient(200deg, #c42ad0, #5a1a6a);
  }
  .theme-mono .logo-art { background: linear-gradient(200deg, #8a8a8a, #111); }
  .logo-rule {
    position: absolute;
    left: 59px; width: 238px;
    height: 2px;
    background: var(--rule);
  }
  .logo-rule--top { top: 292px; }
  .logo-rule--bottom { top: 351px; }
  .logo-name {
    position: absolute;
    left: 59px; width: 238px;
    top: 302px;
    text-align: center;
    font-size: 36px;
    line-height: 44px;
    color: var(--plum);
  }
  .theme-mono .logo-name { color: var(--ink); }
  .logo-tagline {
    position: absolute;
    left: 0; width: 100%;
    top: 362px;
    text-align: center;
    font-size: 17px;
    letter-spacing: 1px;
    color: var(--slate);
  }

  /* Back */
  .back-art {
    position: absolute;
    left: 232px; top: 80px;
    width: 125px; height: 418px;
    border-radius: 70% 30% 20% 60%;
    background: linear-gradient(180deg, #eaa8f2, #9a7aa2);
  }
  .theme-mono .back-art { background: linear-gradient(180deg, #9a9a9a, #ffffff); }
  .back-name {
    position: absolute;
    left: 26px; top: 26px;
    font-size: 44px;
    line-height: 50px;
    color: var(--plum);
  }
  .theme-mono .back-name { color: var(--ink); }
  .credentials {
    position: absolute;
    left: 26px; top: 80px;
    font-size: 13px;
    letter-spacing: 1.5px;
    color: var(--slate);
  }
  .practice {
    position: absolute;
    left: 26px; top: 126px;
    font-size: 17px;
    letter-spacing: 1.2px;
    color: var(--slate);
  }
  .contact-text {
    position: absolute;
    left: 79px;
    margin: 0;
    font-size: 14.5px;
    letter-spacing: 1.3px;
    color: var(--slate);
    white-space: nowrap;
  }
  .contact-icon {
    position: absolute;
    left: 26px;
    width: 30px; height: 26px;
    color: var(--pink);
  }
  .theme-mono .contact-icon { color: var(--slate); }
</style>
</head>
<body>

<!-- Pink version -->
<section class="card card--front-pink theme-pink">
  <div class="logo-art" role="img" aria-label="Quill pen illustration"></div>
  <div class="logo-rule logo-rule--top"></div>
  <div class="logo-name">Marla Vent</div>
  <div class="logo-rule logo-rule--bottom"></div>
  <div class="logo-tagline">Barrister &amp; Solicitor</div>
  <div class="card__band"></div>
</section>

<section class="card card--back-pink theme-pink">
  <div class="back-art" role="img" aria-label="Large decorative feather"></div>
  <div class="back-name">Marla Vent</div>
  <div class="credentials">LL.B., B.C.L., B.F.A.</div>
  <div class="practice">Criminal &amp; Immigration Law</div>

  <svg class="contact-icon" style="top:218px" viewBox="0 0 30 20"><rect x="1" y="1" width="28" height="18" fill="currentColor"/><path d="M1 1 L15 12 L29 1 M1 19 L11 9 M29 19 L19 9" stroke="#fff" stroke-width="1.5" fill="none"/></svg>
  <p class="contact-text" style="top:208px">Street address</p>
  <p class="contact-text" style="top:238px">Toronto, ON</p>
  <p class="contact-text" style="top:268px">Postal Code</p>

  <svg class="contact-icon" style="top:330px" viewBox="0 0 32 24"><path d="M2 10a9 7 0 1 1 5 6l-4 3 1-5a7 7 0 0 1-2-4z" fill="none" stroke="currentColor" stroke-width="1.5"/><path d="M14 14a8 6 0 1 1 14 4l1 4-4-2a8 6 0 0 1-11-6z" fill="#fff" stroke="currentColor" stroke-width="1.5"/><circle cx="18" cy="15" r="1" fill="currentColor"/><circle cx="21" cy="15" r="1" fill="currentColor"/><circle cx="24" cy="15" r="1" fill="currentColor"/></svg>
  <p class="contact-text" style="top:322px">+00 000 000 0000</p>

  <svg class="contact-icon" style="top:382px" viewBox="0 0 30 26"><rect x="8" y="2" width="14" height="7" fill="none" stroke="currentColor" stroke-width="1.5"/><rect x="3" y="9" width="24" height="12" rx="3" fill="none" stroke="currentColor" stroke-width="1.5"/><rect x="8" y="15" width="14" height="9" fill="#fff" stroke="currentColor" stroke-width="1.5"/><path d="M10 18h10M10 21h10" stroke="currentColor"/></svg>
  <p class="contact-text" style="top:373px">+00 000 000 0000</p>

  <svg class="contact-icon" style="top:432px" viewBox="0 0 30 26"><text x="15" y="22" text-anchor="middle" font-size="26" fill="currentColor" font-family="Didact Gothic, sans-serif">@</text></svg>
  <p class="contact-text" style="top:424px">email@email.com</p>

  <div class="card__band"></div>
</section>

<!-- Conservative version -->
<section class="card card--front-mono theme-mono">
  <div class="logo-art" role="img" aria-label="Quill pen illustration"></div>
  <div class="logo-rule logo-rule--top"></div>
  <div class="logo-name">Marla Vent</div>
  <div class="logo-rule logo-rule--bottom"></div>
  <div class="logo-tagline">Barrister &amp; Solicitor</div>
  <div class="card__band"></div>
</section>

<section class="card card--back-mono theme-mono">
  <div class="back-art" role="img" aria-label="Large decorative feather"></div>
  <div class="back-name">Marla Vent</div>
  <div class="credentials">LL.B., B.C.L., B.F.A.</div>
  <div class="practice">Criminal &amp; Immigration Law</div>

  <svg class="contact-icon" style="top:222px" viewBox="0 0 30 20"><rect x="1" y="1" width="28" height="18" fill="currentColor"/><path d="M1 1 L15 12 L29 1 M1 19 L11 9 M29 19 L19 9" stroke="#fff" stroke-width="1.5" fill="none"/></svg>
  <p class="contact-text" style="top:226px">Street address</p>
  <p class="contact-text" style="top:256px">Toronto, ON</p>
  <p class="contact-text" style="top:286px">Postal Code</p>

  <svg class="contact-icon" style="top:326px" viewBox="0 0 32 24"><path d="M2 10a9 7 0 1 1 5 6l-4 3 1-5a7 7 0 0 1-2-4z" fill="none" stroke="currentColor" stroke-width="1.5"/><path d="M14 14a8 6 0 1 1 14 4l1 4-4-2a8 6 0 0 1-11-6z" fill="#fff" stroke="currentColor" stroke-width="1.5"/><circle cx="18" cy="15" r="1" fill="currentColor"/><circle cx="21" cy="15" r="1" fill="currentColor"/><circle cx="24" cy="15" r="1" fill="currentColor"/></svg>
  <p class="contact-text" style="top:326px">+00 000 000 0000</p>

  <svg class="contact-icon" style="top:378px" viewBox="0 0 30 26"><rect x="8" y="2" width="14" height="7" fill="none" stroke="currentColor" stroke-width="1.5"/><rect x="3" y="9" width="24" height="12" rx="3" fill="none" stroke="currentColor" stroke-width="1.5"/><rect x="8" y="15" width="14" height="9" fill="#fff" stroke="currentColor" stroke-width="1.5"/><path d="M10 18h10M10 21h10" stroke="currentColor"/></svg>
  <p class="contact-text" style="top:378px">+00 000 000 0000</p>

  <svg class="contact-icon" style="top:428px" viewBox="0 0 30 26"><text x="15" y="22" text-anchor="middle" font-size="26" fill="currentColor" font-family="Didact Gothic, sans-serif">@</text></svg>
  <p class="contact-text" style="top:429px">email@email.com</p>

  <div class="card__band"></div>
</section>

</body>
</html>
```